FinTech company looking to revamp and expand client-facing interface for our financial models

Pellworth Engines currently has a very simple website that allows clients to interact with our financial models. We are looking to completely redesign the current site and add several extra pages to provide extra functionality. We want the design to have a modern, slick feel, that will work on both a desktop or a tablet. It should be straightforward for clients to move between different pages at any time, and clear from the layout how to interact with the more advanced features. We have included screenshots of existing pages in the attached design brief, as well as sketches of the functionality required by the new pages, but can't provide a direct link to the current site.
Target Market(s)
Professional investors that will be paying to access the interface
Industry/Entity Type
Finance
Number of Pages Required
4 page
Colors
Designer to choose colors to be used in the design.
Look and feel
Each slider illustrates characteristics of the customer's brand and the style your logo design should communicate.

```html
<!DOCTYPE html>
<html lang="en">
<head>
<meta charset="utf-8">
<title>Pellworth Engines – Backtest</title>
<link href="https://fonts.googleapis.com/css2?family=Open+Sans:wght@400;600;700&family=Roboto+Condensed:wght@400;500&display=swap" rel="stylesheet">
<style>
:root{
  --navy:#0a2f5c;
  --navy-btn:#1f4a7a;
  --teal:#0a7163;
  --ink:#111;
  --dark:#1e1e1e;
  --panel:#333;
  --page:#ececec;
  --white:#fff;
  --row-alt:#f0f0f0;
  --muted:#666;
  --blue:#3a6fb5;
  --olive:#b5b82c;
}
*{box-sizing:border-box;margin:0;padding:0}
html,body{width:1200px;height:1122px;overflow:hidden;background:var(--white);font-family:"Open Sans",sans-serif;color:var(--ink)}
.abs{position:absolute}
.page{position:absolute;left:14px;top:14px;width:1172px;height:1094px;background:var(--page)}
.nav{position:absolute;left:14px;top:14px;width:1172px;height:55px;background:var(--white);display:flex;font-weight:700;font-size:13px}
.nav .brand{width:166px;display:flex;align-items:center;padding-left:53px;font-size:17px;border-right:1px solid #e4e4e4;white-space:nowrap}
.nav .range{width:83px;display:flex;align-items:center;justify-content:center;border-right:1px solid #e4e4e4}
.nav .gap{width:125px;border-right:1px solid #e4e4e4}
.nav .item{display:flex;align-items:center;justify-content:center;gap:8px;border-right:1px solid #e4e4e4;font-size:12.5px}
.nav .item.active{background:var(--navy);color:var(--white)}
.card{position:absolute;background:var(--white);box-shadow:0 2px 6px rgba(0,0,0,.12)}
.tabbar{position:absolute;left:97px;top:106px;width:1071px;height:79px;background:#f0f0f0}
.tab{position:absolute;top:148px;height:37px;display:flex;align-items:center;justify-content:center;font-size:12px;font-weight:600}
.chart{position:absolute;left:97px;top:185px;width:1071px;height:313px;background:var(--white)}
.axis-label{font-family:"Open Sans",sans-serif;font-size:11px;fill:#555}
.export{position:absolute;display:flex;align-items:center;gap:6px;color:var(--navy);font-weight:700;font-size:16px}
.table{position:absolute;left:503px;top:582px;width:665px;height:452px;background:var(--white);font-family:"Roboto Condensed",sans-serif;overflow:hidden;box-shadow:0 2px 6px rgba(0,0,0,.1)}
.table .head{display:flex;height:64px;background:var(--dark);color:var(--white);font-family:"Open Sans",sans-serif;font-weight:600;font-size:16px}
.table .head div{width:166px;display:flex;align-items:center;justify-content:center;border-right:1px solid #444}
.table .row{display:flex;height:64px;font-size:16px}
.table .row:nth-child(odd){background:var(--row-alt)}
.table .row div{width:166px;display:flex;align-items:center;justify-content:center}
.table .row div:last-child,.table .head div:last-child{width:129px}
.scroll{position:absolute;background:#d6d6d6}
.stats{position:absolute;left:97px;top:582px;width:369px;height:452px;background:var(--white);font-family:"Roboto Condensed",sans-serif;font-size:16px}
.stats .head{height:64px;background:var(--dark);color:#aaa;display:flex;align-items:center;justify-content:center;font-weight:600;font-size:16px;font-family:"Open Sans",sans-serif}
.overlay{position:absolute;left:14px;top:143px;width:452px;height:845px;background:rgba(48,48,48,.94)}
.mode{position:absolute;top:212px;width:167px;height:42px;border:2px solid var(--white);color:var(--white);display:flex;align-items:center;justify-content:center;font-size:16px;font-weight:600}
.models{position:absolute;left:69px;top:282px;width:342px;height:276px;background:var(--white);border-radius:3px;overflow:hidden}
.search{position:absolute;left:16px;top:9px;width:167px;height:28px;border:1px solid #ccc;border-radius:3px;font-size:14px;padding-left:12px;display:flex;align-items:center;box-shadow:inset 0 1px 2px rgba(0,0,0,.1)}
.select-btn{position:absolute;left:192px;top:9px;width:96px;height:28px;background:var(--teal);color:var(--white);font-weight:600;font-size:14px;display:flex;align-items:center;justify-content:center;border-radius:2px}
.model-list{position:absolute;left:0;top:46px;width:305px}
.model-list div{height:45px;display:flex;align-items:center;padding-left:20px;font-weight:700;font-size:16px;border-top:1px solid #eee}
.model-list .on{background:var(--teal);color:var(--white)}
.add-btn{position:absolute;left:69px;top:578px;width:179px;height:35px;background:var(--navy);color:var(--white);font-weight:700;font-size:13px;display:flex;align-items:center;gap:10px;padding-left:22px;border-radius:2px}
.params{position:absolute;left:69px;top:660px;width:342px;height:258px;background:var(--white);border-radius:3px;overflow:hidden}
.params .head{height:46px;background:#6b6b6b;color:var(--white);font-weight:700;font-size:17px;display:flex;align-items:center;justify-content:center}
.params .field{height:46px;display:flex;align-items:center;padding-left:17px;border-bottom:1px solid #eee;font-weight:700;font-size:16px}
.params .field span{width:89px}
.params .field div{width:223px;height:29px;border:1px solid #ccc;border-radius:3px;font-weight:400;font-size:15px;padding-left:12px;display:flex;align-items:center;box-shadow:inset 0 1px 2px rgba(0,0,0,.1)}
.run{position:absolute;left:100px;top:200px;width:142px;height:44px;background:var(--navy-btn);color:var(--white);font-weight:700;font-size:15px;display:flex;align-items:center;justify-content:center;border-radius:2px}
.side-tab{position:absolute;left:466px;top:450px;width:46px;height:230px;background:#2e2e2e;border-radius:0 4px 4px 0}
.side-tab span{position:absolute;left:12px;top:190px;transform:rotate(-90deg);transform-origin:left top;color:var(--white);font-weight:700;font-size:15px;letter-spacing:1px;white-space:nowrap}
</style>
</head>
<body>
<div class="page"></div>

<nav class="nav">
  <div class="brand">QORBELIX</div>
  <div class="range">250D</div>
  <div class="range">83D</div>
  <div class="range">42D</div>
  <div class="gap"></div>
  <div class="item" style="width:129px;border-left:1px solid #e4e4e4">
    <svg width="22" height="20" viewBox="0 0 22 20"><path d="M2 10 L11 2 L20 10 M5 8 V18 H9 V12 H13 V18 H17 V8" fill="none" stroke="#111" stroke-width="2.4"/></svg>MODELS</div>
  <div class="item" style="width:164px">
    <svg width="22" height="22" viewBox="0 0 22 22"><g fill="none" stroke="#111" stroke-width="1.6"><circle cx="11" cy="11" r="3"/><circle cx="11" cy="11" r="7" stroke-dasharray="2 2"/></g></svg>SENSITIVITIES</div>
  <div class="item" style="width:147px">
    <svg width="22" height="22" viewBox="0 0 22 22"><g fill="none" stroke="#111" stroke-width="1.8"><circle cx="6" cy="6" r="4"/><circle cx="16" cy="6" r="4"/><circle cx="6" cy="16" r="4"/><circle cx="16" cy="16" r="4"/></g></svg>PORTFOLIO</div>
  <div class="item active" style="width:140px">
    <svg width="24" height="20" viewBox="0 0 24 20"><g fill="none" stroke="#fff" stroke-width="1.8"><rect x="2" y="2" width="20" height="16"/><path d="M5 14 L10 8 L14 12 L19 5"/></g></svg>BACKTEST</div>
</nav>

<div class="card" style="left:97px;top:106px;width:1071px;height:392px"></div>
<div class="tabbar"></div>
<div class="tab" style="left:148px;width:143px;background:#1a1a1a;color:#fff">CHART</div>
<div class="tab" style="left:296px;width:84px;color:#555">#1</div>
<div class="tab" style="left:384px;width:84px;color:#555">#2</div>
<div class="tab" style="left:471px;width:84px;background:#fff;color:#333">#3</div>
<div class="tab" style="left:558px;width:83px;background:#1a1a1a;color:#fff">#4</div>
<div class="chart"></div>
<svg class="abs" style="left:0;top:0" width="1200" height="520" viewBox="0 0 1200 520">
  <g stroke="#ececec" stroke-width="1">
    <line x1="110" y1="243" x2="1025" y2="243"/><line x1="110" y1="278" x2="1025" y2="278"/>
    <line x1="110" y1="312" x2="1025" y2="312"/><line x1="110" y1="346" x2="1025" y2="346"/>
    <line x1="110" y1="380" x2="1025" y2="380"/>
    <line x1="591" y1="230" x2="591" y2="415"/><line x1="717" y1="230" x2="717" y2="415"/>
    <line x1="847" y1="230" x2="847" y2="415"/><line x1="976" y1="230" x2="976" y2="415"/>
  </g>
  <line x1="110" y1="415" x2="1025" y2="415" stroke="#888"/>
  <text class="axis-label" x="462" y="439" text-anchor="middle">Nov 2018</text>
  <text class="axis-label" x="591" y="439" text-anchor="middle">Jan 2019</text>
  <text class="axis-label" x="717" y="439" text-anchor="middle">Mar 2019</text>
  <text class="axis-label" x="847" y="439" text-anchor="middle">May 2019</text>
  <text class="axis-label" x="976" y="439" text-anchor="middle">Jul 2019</text>
  <line x1="110" y1="245" x2="480" y2="245" stroke="var(--olive)" stroke-width="6" stroke-linecap="round" stroke-dasharray="0 7"/>
  <line x1="700" y1="245" x2="955" y2="245" stroke="var(--olive)" stroke-width="6" stroke-linecap="round" stroke-dasharray="0 7"/>
  <line x1="576" y1="243" x2="980" y2="243" stroke="var(--blue)" stroke-width="6" stroke-linecap="round" stroke-dasharray="0 6"/>
  <g fill="var(--blue)">
    <circle cx="470" cy="254" r="3"/><circle cx="474" cy="266" r="3"/><circle cx="485" cy="277" r="3"/><circle cx="476" cy="280" r="3"/>
    <circle cx="533" cy="262" r="3"/><circle cx="536" cy="258" r="3"/><circle cx="541" cy="250" r="3"/><circle cx="549" cy="248" r="3"/><circle cx="557" cy="251" r="3"/>
    <circle cx="522" cy="342" r="3"/><circle cx="525" cy="340" r="3"/><circle cx="521" cy="352" r="3"/><circle cx="505" cy="372" r="3"/><circle cx="500" cy="372" r="3"/><circle cx="517" cy="382" r="3"/><circle cx="490" cy="390" r="3"/><circle cx="494" cy="397" r="3"/>
    <circle cx="420" cy="375" r="3"/><circle cx="428" cy="380" r="3"/><circle cx="440" cy="390" r="3"/><circle cx="450" cy="405" r="3"/><circle cx="435" cy="410" r="3"/>
  </g>
  <g fill="var(--olive)">
    <circle cx="530" cy="247" r="3"/><circle cx="537" cy="250" r="3"/><circle cx="560" cy="256" r="3"/>
    <circle cx="520" cy="322" r="3"/><circle cx="526" cy="311" r="3"/><circle cx="522" cy="318" r="3"/><circle cx="511" cy="364" r="3"/><circle cx="503" cy="358" r="3"/><circle cx="490" cy="397" r="3"/><circle cx="481" cy="405" r="3"/><circle cx="475" cy="408" r="3"/><circle cx="469" cy="409" r="3"/>
    <circle cx="566" cy="404" r="3"/><circle cx="568" cy="408" r="3"/><circle cx="580" cy="403" r="3"/><circle cx="584" cy="406" r="3"/><circle cx="592" cy="398" r="3"/><circle cx="600" cy="395" r="3"/><circle cx="606" cy="399" r="3"/><circle cx="611" cy="403" r="3"/><circle cx="620" cy="404" r="3"/>
    <circle cx="626" cy="376" r="3"/><circle cx="630" cy="381" r="3"/><circle cx="636" cy="368" r="3"/><circle cx="639" cy="368" r="3"/><circle cx="641" cy="336" r="3"/><circle cx="643" cy="349" r="3"/><circle cx="637" cy="301" r="3"/><circle cx="650" cy="301" r="3"/><circle cx="670" cy="314" r="3"/>
    <circle cx="653" cy="266" r="3"/><circle cx="655" cy="260" r="3"/><circle cx="668" cy="262" r="3"/><circle cx="682" cy="262" r="3"/><circle cx="684" cy="274" r="3"/><circle cx="688" cy="285" r="3"/><circle cx="696" cy="296" r="3"/><circle cx="690" cy="296" r="3"/>
    <circle cx="698" cy="335" r="3"/><circle cx="676" cy="376" r="3"/><circle cx="681" cy="386" r="3"/>
    <circle cx="700" cy="253" r="3"/><circle cx="706" cy="252" r="3"/><circle cx="712" cy="262" r="3"/><circle cx="715" cy="258" r="3"/><circle cx="723" cy="250" r="3"/><circle cx="728" cy="255" r="3"/><circle cx="730" cy="249" r="3"/>
    <circle cx="410" cy="320" r="3"/><circle cx="420" cy="330" r="3"/><circle cx="430" cy="355" r="3"/><circle cx="415" cy="365" r="3"/>
  </g>
  <g fill="#5a9a2a"><circle cx="955" cy="412" r="3"/><circle cx="960" cy="412" r="3"/><circle cx="965" cy="412" r="3"/></g>
  <text x="1077" y="245" font-family="Georgia,serif" font-size="11" fill="#333">Names</text>
  <g>
    <circle cx="1062" cy="241" r="3" fill="#8ab4e0"/><circle cx="1062" cy="258" r="3" fill="#f0b07a"/>
    <circle cx="1062" cy="276" r="3" fill="#4f9a3a"/><circle cx="1062" cy="293" r="3" fill="#e88a8a"/>
    <circle cx="1062" cy="311" r="3" fill="#c8a0d8"/><circle cx="1062" cy="328" r="3" fill="#b89a8a"/>
    <circle cx="1062" cy="345" r="3" fill="#f0a8d0"/><circle cx="1062" cy="362" r="3" fill="#bbb"/>
    <circle cx="1062" cy="379" r="3" fill="#c8c830"/><circle cx="1062" cy="396" r="3" fill="#7ad0e0"/>
    <circle cx="1062" cy="413" r="3" fill="#2b5ca8"/>
  </g>
  <path d="M614 168 v14 l-3 -3 l-3 3 l3 5 c1 3 3 5 6 5 h6 c3 0 4 -2 4 -5 v-7 c0 -2 -3 -2 -3 0 c0 -2 -3 -2 -3 0 c0 -2 -3 -2 -3 0 v-12 c0 -2 -4 -2 -4 0z" fill="#fff" stroke="#000" stroke-width="1.2"/>
</svg>

<div class="stats">
  <div class="head">Stats</div>
  <div class="abs" style="left:0;top:320px;width:332px;height:64px;display:flex;align-items:center;color:#333"><span style="width:166px;text-align:center">Stat 5</span><span style="width:166px;text-align:center">-3</span></div>
  <div class="abs" style="left:0;top:384px;width:332px;height:64px;display:flex;align-items:center;background:var(--row-alt)"><span style="width:166px;text-align:center">Stat 6</span><span style="width:166px;text-align:center">30%</span></div>
  <div class="scroll" style="left:332px;top:64px;width:37px;height:388px"></div>
  <div class="abs" style="left:341px;top:88px;width:18px;height:342px;border-radius:9px;background:#fff"></div>
</div>
<div class="export" style="left:385px;top:548px;color:#555"><svg width="24" height="22" viewBox="0 0 24 22"><path d="M10 4 H3 V19 H18 V13 M12 12 L21 3 M15 3 H21 V9" fill="none" stroke="currentColor" stroke-width="2"/></svg>Export</div>

<div class="export" style="left:1083px;top:548px"><svg width="24" height="22" viewBox="0 0 24 22"><path d="M10 4 H3 V19 H18 V13 M12 12 L21 3 M15 3 H21 V9" fill="none" stroke="currentColor" stroke-width="2"/></svg>Export</div>
<div class="table">
  <div class="head"><div>Open</div><div>Close</div><div>Size</div><div>Return</div></div>
  <div>
    <div class="row"><div>2018-04-05</div><div>2018-04-07</div><div>13</div><div>5%</div></div>
    <div class="row"><div>2018-04-05</div><div>2018-04-07</div><div>12</div><div>7%</div></div>
    <div class="row"><div>2018-04-05</div><div>2018-04-07</div><div>15</div><div>6%</div></div>
    <div class="row"><div>2018-04-05</div><div>2018-04-07</div><div>16</div><div>9%</div></div>
    <div class="row"><div>2018-04-05</div><div>2018-04-07</div><div>12</div><div>8%</div></div>
    <div class="row"><div>2018-04-05</div><div>2018-04-07</div><div>19</div><div>6%</div></div>
  </div>
  <div class="scroll" style="left:628px;top:64px;width:37px;height:388px"></div>
  <div class="abs" style="left:637px;top:88px;width:18px;height:342px;border-radius:9px;background:#fff"></div>
  <div class="abs" style="left:637px;top:88px;width:18px;height:80px;border-radius:9px;background:linear-gradient(#999,#666)"></div>
</div>

<div class="overlay"></div>
<div class="mode" style="left:69px;background:var(--navy)">Mode 1</div>
<div class="mode" style="left:244px">Mode 2</div>
<div class="models">
  <div class="search">Model name</div>
  <div class="select-btn">Select</div>
  <div class="model-list">
    <div>Model 1</div><div>Model 2</div><div class="on">Model 3</div><div>Model 4</div><div>Model 5</div>
  </div>
  <div class="abs" style="left:305px;top:46px;width:37px;height:230px;background:#d6d6d6"></div>
  <div class="abs" style="left:314px;top:70px;width:18px;height:188px;border-radius:9px;background:linear-gradient(#888,#111 50%,#000)"></div>
</div>
<svg class="abs" style="left:180px;top:448px" width="28" height="34" viewBox="0 0 28 34"><path d="M6 2 v16 l-3 -3 l-3 3 l4 6 c1 4 4 7 8 7 h6 c4 0 5 -3 5 -6 v-8 c0 -2 -3 -2 -3 0 c0 -2 -3 -2 -3 0 c0 -2 -3 -2 -3 0 v-15 c0 -3 -4 -3 -4 0z" fill="#fff" stroke="#000" stroke-width="1.3"/></svg>
<div class="add-btn"><svg width="22" height="22" viewBox="0 0 22 22"><g fill="none" stroke="#fff" stroke-width="1.6"><circle cx="11" cy="11" r="9"/><path d="M11 6 V16 M6 11 H16"/></g></svg>ADD A MODEL</div>
<div class="params">
  <div class="head">Parameters:</div>
  <div class="field"><span>Entry:</span><div>0.5</div></div>
  <div class="field"><span>Exit:</span><div>-0.3</div></div>
  <div class="field"><span>Lookback:</span><div>5</div></div>
  <div class="run">RUN</div>
</div>
<div class="side-tab"><span>SELECT A MODEL</span></div>
<svg class="abs" style="left:498px;top:551px" width="28" height="28" viewBox="0 0 28 28"><circle cx="14" cy="14" r="12" fill="var(--navy)" stroke="#fff" stroke-width="2"/><path d="M20 14 H9 M13 9 L8 14 L13 19" fill="none" stroke="#fff" stroke-width="2.2"/></svg>
</body>
</html>
```